Business card

We need a business card design for our company based in Auckland , New Zealand called 'Ridge + Studio Ltd'. We provide architectural services. We would like to see designs that use the max. three colours (such as white, black, grey) The final design should communicate financial safety and growth."
Also I will provide our company logo. I would like to the logo to be embeded onto our business card.

Target Market(s)

new residential house, alteration & addition & light commericila design & drafting service

Industry/Entity Type

Architecture

Contact Information for Business Card

Company name: ridge + studio Ltd.
Name: Mark Delford
Job title: architectural designer & Design LBP
email address: mark@ridgelinestudio.co.nz
mobile number: 02 5163 2290
web site: www.ridgelinestudio.co.nz

Requirements
Must have
• My project must have..
• - embeded logo (attached company logo)
• I don't have a bigger version for our company logo, but I have one old one, so you can remove the word from it)
• - insert the attached small BKTW logo & LBP logo
• - creative, simple and clear business card.
• - Max. three colours
Nice to have
• - Here are the samples I would like to share with you: http://www.plimvora.com/blog/minimalistic-business-card-designs/
• I would like to have my business card like one of the creation.
Should not have
• TBA

```html
<!DOCTYPE html>
<html lang="en">
<head>
<meta charset="utf-8">
<title>Ridgeline Studio — Business Card</title>
<link rel="stylesheet" href="https://fonts.googleapis.com/css2?family=Roboto:wght@500&family=Open+Sans:wght@400;700&display=swap">
<style>
  :root {
    --backdrop: #e9e6e3;
    --card: #ffffff;
    --ink: #111111;
    --arc-outer: #000000;
    --arc-inner: #242424;
    --on-dark: #ffffff;
    --badge: #2b2b2b;
  }
  html, body {
    margin: 0;
    width: 1200px;
    height: 900px;
    overflow: hidden;
    background: var(--backdrop);
  }
  .canvas { position: relative; width: 1200px; height: 900px; }
  .card {
    position: absolute;
    background: var(--card);
    overflow: hidden;
    box-shadow: 0 6px 18px rgba(0,0,0,0.15);
  }
  .card--front { left: 238px; top: 62px; width: 555px; height: 342px; }
  .card--back  { left: 457px; top: 518px; width: 560px; height: 343px; }

  .company-name {
    position: absolute;
    left: 0; right: 0;
    margin: 0;
    text-align: center;
    font-family: "Roboto", sans-serif;
    font-weight: 500;
    color: var(--ink);
    white-space: nowrap;
  }
  .card--front .company-name { top: 28px; font-size: 33px; line-height: 40px; }
  .card--back .company-name { top: 161px; font-size: 23px; line-height: 30px; }

  .front-arc { position: absolute; left: 0; top: 0; }

  .contact {
    position: absolute;
    left: 0; right: 0;
    top: 170px;
    text-align: center;
    font-family: "Open Sans", sans-serif;
    color: var(--on-dark);
  }
  .contact__name { margin: 0; font-weight: 700; font-size: 18px; line-height: 24px; letter-spacing: 0.3px; }
  .contact__role { margin: 4px 0 0; font-size: 14.5px; line-height: 20px; }
  .contact__lines { margin: 23px 0 0; font-size: 16px; line-height: 23px; font-style: normal; }

  .brand-mark {
    position: absolute;
    left: 215px; top: 22px;
    width: 130px; height: 130px;
  }
  .badges {
    position: absolute;
    left: 0; right: 0; top: 224px;
    display: flex;
    justify-content: center;
    align-items: center;
    gap: 22px;
  }
  .badge--membership { width: 114px; height: 86px; background: var(--badge); }
  .badge--licence { width: 95px; height: 95px; border-radius: 50%; background: var(--badge); }
</style>
</head>
<body>
<main class="canvas">
  <section class="card card--front">
    <h1 class="company-name">Ridgeline Studio</h1>
    <svg class="front-arc" width="555" height="342" viewBox="0 0 555 342" aria-hidden="true">
      <ellipse cx="278" cy="342" rx="277" ry="259" fill="var(--arc-outer)"/>
      <ellipse cx="302" cy="342" rx="248" ry="221" fill="var(--arc-inner)"/>
    </svg>
    <div class="contact">
      <p class="contact__name">MARK DELFORD</p>
      <p class="contact__role">Architectural designer &amp; Design LBP</p>
      <address class="contact__lines">
        02 5163 2290<br>
        mark@ridgelinestudio.co.nz<br>
        www.ridgelinestudio.co.nz
      </address>
    </div>
  </section>

  <section class="card card--back">
    <svg class="brand-mark" viewBox="0 0 130 130" aria-hidden="true">
      <circle cx="65" cy="65" r="58" fill="none" stroke="var(--ink)" stroke-width="8"/>
    </svg>
    <p class="company-name">Ridgeline Studio</p>
    <div class="badges">
      <div class="badge badge--membership" role="img" aria-label="BKTW professional member badge"></div>
      <div class="badge badge--licence" role="img" aria-label="Licensed practitioner badge"></div>
    </div>
  </section>
</main>
</body>
</html>
```